Party Favors and Decorations Business Needs A Business Card Design

We are in need of a Logo design and business card design for a new small business called Bright Lantern Designs. We create party decorations and favours for Bridal Showers, Baby Showers, Weddings Birthdays etc. This is a very personalized service based on Clients theme, colour, and style. We are looking for a high end elegant look. I have attached a file to the style I like including the type of paper.

Target Market(s)

women, young adults, expectant mothers, mothers

Industry/Entity Type

Small Business

Contact Information for Business Card

Bright Lantern Designs Essex, ON 519-847-2061 brightlanterndesigns.ca karen@brightlanterngiftbox.com find us on Chatterly

Logo Text

Bright Lantern Designs

Font styles to use
Script

Requirements
Must have
• Name, email, web address, phone number
Should not have
• cutesy graphics

```html
<!DOCTYPE html>
<html lang="en">
<head>
<meta charset="utf-8">
<title>Bright Lantern Designs – Business Card</title>
<link rel="stylesheet" href="https://fonts.googleapis.com/css2?family=Arimo:wght@400&family=Dancing+Script:wght@700&display=swap">
<style>
  :root {
    --backdrop: #e6e3de;
    --card-dark: #0c0c0c;
    --card-light: #f7f7f6;
    --ink-light: #ffffff;
    --ink-dark: #161616;
    --ink-muted: #d8d8d8;
  }
  * { box-sizing: border-box; margin: 0; padding: 0; }
  html, body { width: 1200px; height: 892px; overflow: hidden; }
  body {
    background: var(--backdrop);
    display: flex;
    align-items: center;
    justify-content: center;
    gap: 70px;
  }
  .card {
    width: 400px;
    height: 640px;
    border-radius: 4px;
    position: relative;
    box-shadow: 0 10px 30px rgba(0,0,0,.18);
  }
  .card--front { background: var(--card-dark); color: var(--ink-light); }
  .card--back  { background: var(--card-light); color: var(--ink-dark); }

  .brand-name {
    position: absolute;
    left: 20px; right: 20px;
    text-align: center;
    font-family: "Arimo", sans-serif;
    font-weight: 400;
    font-size: 29px;
    line-height: 1.2;
    white-space: nowrap;
  }
  .card--front .brand-name { top: 110px; }
  .card--back .brand-name  { bottom: 120px; }

  .holder {
    position: absolute;
    top: 270px;
    left: 0; right: 0;
    text-align: center;
  }
  .holder__name {
    font-family: "Dancing Script", cursive;
    font-weight: 700;
    font-size: 40px;
    line-height: 1.1;
  }
  .holder__title {
    font-family: "Arimo", sans-serif;
    font-size: 15px;
    color: var(--ink-muted);
    margin-top: 4px;
  }

  .contact {
    position: absolute;
    left: 32px;
    bottom: 56px;
    list-style: none;
    font-family: "Arimo", sans-serif;
    font-size: 21px;
    line-height: 1.45;
  }
</style>
</head>
<body>
  <section class="card card--front" aria-label="Business card front">
    <p class="brand-name">Bright Lantern Designs</p>
    <div class="holder">
      <p class="holder__name">Employee name</p>
      <p class="holder__title">Managing Director</p>
    </div>
    <ul class="contact">
      <li>519-847-2061</li>
      <li>www.brightlanterndesigns.ca</li>
      <li>karen@brightlanterngiftbox.com</li>
    </ul>
  </section>

  <section class="card card--back" aria-label="Business card back">
    <p class="brand-name">Bright Lantern Designs</p>
  </section>
</body>
</html>
```